Business card for a Exhibition booth fabrication company

Hi. My company would like to change our corporate name card. We are an events and Exhibition stand builder company. We would like our corporate name card to resonate what we do. I need someone to create something unique that relates to the industry that I am in. The graphic designer should be creative to incorporate the elements of my industry and try to blend in well in the design of the card. Our aim is to ensure that we are unique and our card can look different from our competitors.
Updates

Target Market(s)

Marketing and events manager from all companies

Contact Information for Business Card

The business card should have the following details:
Name
Job Title
Email
Website

Colors

Designer to choose colors to be used in the design.

Requirements
Must have
• The card must be look something that is relevant to the service that I am providing. My website is: www.velmora-buildworks.com
• You can see my website to get more information on what service that I am doing
Nice to have
• On the back of my card, I would like to have a globe image with the incorporation of my company logo. This is to indicate that my services can be done in any part of the world.

```html
<!DOCTYPE html>
<html lang="en">
<head>
<meta charset="utf-8">
<title>Velmora Buildworks – Business Card</title>
<link rel="stylesheet" href="https://fonts.googleapis.com/css2?family=Arimo:wght@400;700&family=Open+Sans:wght@400&display=swap">
<style>
  :root {
    --brand-red: #ed1c24;
    --map-red: #f2555b;
    --swoosh-grey: #636466;
    --text-grey: #5b5b5d;
    --silver: #b9b9bb;
    --white: #ffffff;
    --bg-left: #dcdddf;
    --bg-right: #a6a7a9;
  }
  * { margin: 0; padding: 0; box-sizing: border-box; }
  html, body { width: 1200px; height: 1117px; overflow: hidden; }
  body {
    position: relative;
    background: linear-gradient(90deg, var(--bg-left), var(--bg-right));
    font-family: "Open Sans", sans-serif;
  }
  .card {
    position: absolute;
    left: 222px;
    width: 755px;
    height: 432px;
    border-radius: 30px;
    overflow: hidden;
  }
  .card--front { top: 79px; background: var(--white); }
  .card--back  { top: 573px; background: var(--brand-red); }
  .card__shapes { position: absolute; inset: 0; width: 100%; height: 100%; }

  .brand-name {
    position: absolute;
    left: 55px;
    top: 140px;
    font-family: "Arimo", sans-serif;
    font-weight: 700;
    font-size: 25px;
    letter-spacing: 2px;
    color: var(--text-grey);
    white-space: nowrap;
  }
  .person { position: absolute; left: 52px; top: 242px; }
  .person__name {
    font-family: "Arimo", sans-serif;
    font-weight: 700;
    font-size: 26px;
    letter-spacing: 0.5px;
    color: var(--brand-red);
    line-height: 1.1;
  }
  .person__title {
    font-family: "Arimo", sans-serif;
    font-size: 19px;
    letter-spacing: 0.5px;
    color: var(--text-grey);
    margin-top: 5px;
  }
  .contacts {
    position: absolute;
    right: 26px;
    top: 270px;
    list-style: none;
    color: var(--white);
    font-size: 17.5px;
    text-align: right;
  }
  .contacts li {
    display: flex;
    justify-content: flex-end;
    align-items: center;
    gap: 10px;
    height: 34px;
  }
  .contacts li.contacts__address { margin-top: 8px; }
  .contacts svg { width: 20px; height: 20px; flex: none; }

  .world-area {
    position: absolute;
    left: 0; top: 72px;
    width: 755px; height: 240px;
    background: radial-gradient(ellipse at center, rgba(255,255,255,0.16), rgba(255,255,255,0.05) 70%, rgba(255,255,255,0));
  }
  .back-brand {
    position: absolute;
    left: 0; right: 0;
    top: 270px;
    text-align: center;
    font-family: "Arimo", sans-serif;
    font-weight: 700;
    font-size: 27px;
    letter-spacing: 4px;
    color: var(--silver);
  }
  .back-web {
    position: absolute;
    left: 0; right: 0;
    top: 387px;
    text-align: center;
    font-size: 20px;
    letter-spacing: 4.5px;
    color: var(--white);
  }
</style>
</head>
<body>

<section class="card card--front">
  <svg class="card__shapes" viewBox="0 0 646 370" preserveAspectRatio="none" aria-hidden="true">
    <path d="M646,10 C560,150 420,300 0,318 L0,370 L646,370 Z" fill="var(--brand-red)"/>
    <path d="M0,270 C120,322 320,300 455,205 C330,310 140,332 0,312 Z" fill="var(--swoosh-grey)"/>
  </svg>

  <div class="brand-name">VELMORA BUILDWORKS</div>

  <div class="person">
    <div class="person__name">DANIEL HARCOURT</div>
    <div class="person__title">PRESIDENT</div>
  </div>

  <ul class="contacts">
    <li>012-345-6789
      <svg viewBox="0 0 24 24" aria-hidden="true"><path fill="#fff" d="M6.6 10.8c1.4 2.8 3.8 5.1 6.6 6.6l2.2-2.2c.3-.3.7-.4 1-.2 1.1.4 2.3.6 3.6.6.6 0 1 .4 1 1V20c0 .6-.4 1-1 1C10.6 21 3 13.4 3 4c0-.6.4-1 1-1h3.5c.6 0 1 .4 1 1 0 1.3.2 2.5.6 3.6.1.3 0 .7-.2 1z"/></svg>
    </li>
    <li>info@velmora-buildworks.com
      <svg viewBox="0 0 24 24" aria-hidden="true"><rect x="3" y="6" width="18" height="12" fill="#fff"/><path d="M3 6l9 7 9-7M3 18l7-6M21 18l-7-6" stroke="var(--brand-red)" stroke-width="1.4" fill="none"/></svg>
    </li>
    <li>www.velmora-buildworks.com
      <svg viewBox="0 0 24 24" aria-hidden="true"><g fill="none" stroke="#fff" stroke-width="1.6"><circle cx="12" cy="12" r="9"/><ellipse cx="12" cy="12" rx="4" ry="9"/><path d="M3 12h18M5 7.5h14M5 16.5h14"/></g></svg>
    </li>
    <li class="contacts__address">Street Name, City Name, Zipcode - 01234</li>
  </ul>
</section>

<section class="card card--back">
  <div class="world-area" role="img" aria-label="Faint world map spanning the card"></div>
  <div class="back-brand">VELMORA BUILDWORKS</div>
  <div class="back-web">www.velmora-buildworks.com</div>
</section>

</body>
</html>
```